IT Freelancer (Consulting, trainer and project manager) needed letterhead

As a freelancer for IT Trainingswhip, consulting and project management I need a letterhead design. What is desired is a design that fits the existing logo (see Annex). It is functional, reliable, and equal time wirkenn Agil and modern. The whole is in color, as well as printed out to make a good impression on a black and white printer. The whole is to the existing Cooperate design (business card, homepage, logo) fit. Therefore, the choice of colors.
Updates

Target Market(s)

Customers such as medium-sized enterprises, training institutions

Industry/Entity Type

Consulting

Colors
0455a3
3277b5
85abd2
cfdfed
34a6d7
32a6d6
249fd4
0792cd
85cae6

Requirements
Must have
• Must include logo (see Annex) address (Brunnerweg 14, 95617 Mittelfeld, Germany). Must seriously and act simultaneously Agil. Design should (even) be adaptable (signature, address, etc.) design must look good on a black / white laser

```html
<!DOCTYPE html>
<html lang="en">
<head>
<meta charset="utf-8">
<title>Lukas Brenner – Letterhead</title>
<link rel="stylesheet" href="https://fonts.googleapis.com/css2?family=Carlito:wght@400;700&display=swap">
<style>
  :root {
    --navy: #0455a3;
    --blue-mid: #3277b5;
    --sky: #34a6d7;
    --mist: #e3ecf5;
    --ink: #1a1a1a;
    --paper: #ffffff;
    --backdrop: #c0c0c0;
  }
  * { box-sizing: border-box; margin: 0; padding: 0; }
  html, body {
    width: 1200px; height: 1200px; overflow: hidden;
    background: var(--backdrop);
    font-family: "Carlito", "Calibri", sans-serif;
  }
  .sheet-frame {
    position: absolute; left: 176px; top: 0;
    width: 772px; height: 1092px;
    transform: scale(1.0989); transform-origin: 0 0;
  }
  .sheet {
    position: relative; width: 772px; height: 1092px;
    background: var(--paper); overflow: hidden; color: var(--ink);
  }
  .header-wave, .corner-disc { position: absolute; }
  .header-wave { left: 0; top: 0; }
  .corner-disc { left: 456px; top: 794px; }

  .brand { position: absolute; left: 66px; top: 44px; width: 160px; text-align: center; }
  .brand-mark {
    width: 92px; height: 92px; margin: 0 auto 10px;
    border-radius: 50%; background: var(--navy);
  }
  .brand-name {
    color: var(--navy); font-weight: 700; font-size: 23px;
    line-height: 21px; letter-spacing: 1px;
  }

  .contact {
    position: absolute; left: 558px; top: 42px;
    color: #fff; font-size: 10.5px; line-height: 19.5px;
  }
  .contact-row { display: flex; align-items: center; gap: 6px; }
  .contact-row svg { width: 10px; height: 10px; flex: none; }
  .contact-address { margin-top: 1px; line-height: 14px; }

  .recipient { position: absolute; left: 79px; top: 243px; font-size: 14px; line-height: 27.3px; }
  .recipient .strong { font-weight: 700; }
  .salutation { position: absolute; left: 76px; top: 419px; font-size: 14px; font-weight: 700; }
  .letter-body { position: absolute; left: 76px; top: 472px; width: 640px; font-size: 14px; line-height: 27.3px; }
  .letter-body p + p { margin-top: 27.3px; }
  .closing { position: absolute; left: 76px; top: 882px; font-size: 14px; }
  .signature {
    position: absolute; left: 76px; top: 908px; width: 192px; height: 70px;
    background: linear-gradient(90deg, #f1f1f1, #e6e6e6); border-radius: 4px;
  }
  .sender-title { position: absolute; left: 76px; top: 991px; font-size: 14px; }
</style>
</head>
<body>
<div class="sheet-frame">
  <div class="sheet">
    <svg class="header-wave" width="772" height="200" viewBox="0 0 772 200" aria-hidden="true">
      <path d="M216 0 C350 100 500 192 640 190 C700 189 740 172 772 150 L772 0 Z" fill="var(--sky)"/>
      <path d="M216 0 C350 90 500 175 640 170 C700 168 740 148 772 124 L772 0 Z" fill="var(--navy)"/>
    </svg>

    <svg class="corner-disc" width="316" height="300" viewBox="0 0 316 300" aria-hidden="true">
      <circle cx="180" cy="180" r="180" fill="var(--mist)"/>
    </svg>

    <div class="brand">
      <div class="brand-mark"></div>
      <div class="brand-name">LUKAS<br>BRENNER</div>
    </div>

    <div class="contact">
      <div class="contact-row">
        <svg viewBox="0 0 10 10"><path d="M1 3 Q5 0 9 3 L8 4.5 L6.5 3.8 L6.5 3 Q5 2.5 3.5 3 L3.5 3.8 L2 4.5 Z M2.5 5 H7.5 L8.5 9 H1.5 Z" fill="#fff"/></svg>
        <span>+00 2344 5678</span>
      </div>
      <div class="contact-row">
        <svg viewBox="0 0 10 10"><rect x="1" y="2.5" width="8" height="6" fill="none" stroke="#fff" stroke-width="1.2"/><path d="M1 2.5 L5 6 L9 2.5" fill="none" stroke="#fff" stroke-width="1.2"/></svg>
        <span>info@lukasbrenner.com</span>
      </div>
      <div class="contact-row">
        <svg viewBox="0 0 10 10"><circle cx="5" cy="5" r="4" fill="none" stroke="#fff"/><ellipse cx="5" cy="5" rx="1.8" ry="4" fill="none" stroke="#fff" stroke-width="0.8"/><path d="M1 5 H9" stroke="#fff" stroke-width="0.8"/></svg>
        <span>www.lukasbrenner.com</span>
      </div>
      <div class="contact-address">Brunnerweg 14<br>95617 Mittelfeld<br>Germany</div>
    </div>

    <div class="recipient">
      <div>To</div>
      <div class="strong">Lorem Ipsum is simply</div>
      <div>Lorem Ipsum</div>
      <div>Address Line 1 text of the printing and</div>
      <div>Address Line 2 text</div>
    </div>

    <div class="salutation">Dear Alex,</div>

    <div class="letter-body">
      <p>&nbsp;dummy text of the printing and typesetting industry. Lorem Ipsum has been the industry's standard<br>dummy text ever since the 1500s, when an unknown printer took a galley of type and scrambled it<br>to make a type specimen book. It has survived not only five centuries, but also the leap into elec-<br>tronic typesetting, remaining essentially unchanged.</p>
      <p>It is a long established fact that a reader will be distracted by the readable content of a page when<br>looking at its layout. The point of using Lorem Ipsum is that it has a more-or-less normal distribution<br>of letters, as opposed to using 'Content here, content here', making it look like readable English.<br>Many desktop publishing packages and web page editors now.</p>
      <p>&nbsp;Contrary to popular belief, Lorem Ipsum is not simply random text. It has roots in a piece of classical<br>Latin literature from 45 BC, making it over 2000 years old. Henry Caldwell, a Latin professor at<br>Ashford Hill College in Vermont, looked up one of the more obscure Latin words, consectetur,<br>from a Lorem Ipsum passage,</p>
    </div>

    <div class="closing">Lorem Ipsum</div>
    <div class="signature" role="img" aria-label="Handwritten signature"></div>
    <div class="sender-title">Lorem Ipsum is a dummy</div>
  </div>
</div>
</body>
</html>
```